you will use Ai to Copy the website Brivanta.com to come up with the basic frame work and it will give you the understanding of how I would like Kelbrava.com to be like. Kelbrava.com is a peer to peer rv rental site very similar to both of the other rv rental sites the difference is that are commission based 20% and above per rental and we will be one flat monthly rate and they keep all the earnings. Below is photo that will help you with the color scheme and the look and feel of the design

1 page

```html
<!DOCTYPE html>
<html lang="en">
<head>
<meta charset="utf-8">
<title>Kelbrava.com — Peer-to-Peer RV Rentals</title>
<link rel="stylesheet" href="https://fonts.googleapis.com/css2?family=Inter:wght@400;500;600;700;800&display=swap">
<style>
:root{
  --navy:#0f1e38;
  --navy-2:#13264a;
  --green:#8aa633;
  --green-dark:#7a9529;
  --cream:#f4f3ee;
  --band:#ecebdf;
  --ink:#16233d;
  --muted:#6b7280;
  --line:#e4e4e0;
  --white:#ffffff;
}
*{box-sizing:border-box;margin:0;padding:0}
html,body{width:1200px;height:2871px;overflow:hidden}
body{font-family:"Inter",Arial,sans-serif;background:var(--cream);color:var(--ink);position:relative}
.abs{position:absolute}
svg{display:block}

/* Nav */
.site-nav{position:absolute;left:0;top:0;width:1200px;height:73px;background:var(--navy);display:flex;align-items:center}
.brand{position:absolute;left:33px;top:18px;font-weight:800;font-size:27px;color:var(--white);letter-spacing:-.5px;display:flex;align-items:center;gap:9px}
.brand-dot{width:14px;height:14px;border-radius:50%;background:var(--green)}
.nav-links{position:absolute;left:264px;top:28px;display:flex;gap:26px;font-size:14.5px;font-weight:600;color:var(--white)}
.nav-links span{display:flex;align-items:center;gap:8px}
.login{position:absolute;left:1007px;top:28px;font-size:14.5px;font-weight:600;color:var(--white)}
.btn{display:flex;align-items:center;justify-content:center;border-radius:4px;font-weight:600;font-size:15px;color:var(--white)}
.btn-green{background:var(--green)}
.btn-outline{border:1.5px solid rgba(255,255,255,.85)}
.signup{position:absolute;left:1075px;top:17px;width:90px;height:39px;font-size:14.5px}

/* Hero */
.hero{position:absolute;left:0;top:73px;width:1200px;height:595px;
  background:linear-gradient(180deg,#6f7f8f 0%,#8c96a0 18%,#4e6157 40%,#2e4a3a 62%,#4a5b55 80%,#3a4039 100%)}
.hero-shade{position:absolute;inset:0;background:linear-gradient(90deg,rgba(10,20,30,.55) 0%,rgba(10,20,30,.2) 50%,rgba(0,0,0,0) 75%)}
.hero h1{position:absolute;left:61px;top:148px;font-size:63px;line-height:74px;font-weight:700;color:var(--white);letter-spacing:-1px}
.hero p{position:absolute;left:61px;top:311px;width:440px;font-size:18px;line-height:31px;color:var(--white)}
.hero .b1{position:absolute;left:61px;top:396px;width:151px;height:49px}
.hero .b2{position:absolute;left:232px;top:396px;width:157px;height:49px}

/* Search */
.search{position:absolute;left:61px;top:609px;width:1075px;height:121px;background:var(--white);border-radius:12px;box-shadow:0 6px 24px rgba(15,30,56,.10)}
.field{position:absolute;top:37px}
.field .label{font-size:12px;font-weight:600;color:var(--ink)}
.field .value{margin-top:10px;font-size:14px;color:var(--muted);display:flex;align-items:center;justify-content:space-between}
.divider{position:absolute;top:28px;width:1px;height:64px;background:var(--line)}
.search-btn{position:absolute;left:926px;top:38px;width:123px;height:47px;font-size:15px}

/* Section headings */
.h2{position:absolute;left:66px;font-size:25px;font-weight:700;color:var(--ink);letter-spacing:-.3px}
.next{position:absolute;width:44px;height:44px;border-radius:50%;background:var(--white);box-shadow:0 2px 10px rgba(0,0,0,.12);display:flex;align-items:center;justify-content:center}

/* RV types */
.type{position:absolute;top:847px;width:170px;text-align:center}
.type .pic{height:112px;border-radius:14px;margin:0 10px;background:linear-gradient(180deg,#d9d9d6,#8d8f92)}
.type .name{margin-top:16px;font-size:17px;font-weight:600;line-height:25px;color:var(--ink)}

/* Destinations */
.dest{position:absolute;top:1169px;width:197px;height:213px;border-radius:8px;overflow:hidden}
.dest .shade{position:absolute;inset:0;background:linear-gradient(180deg,rgba(0,0,0,0) 55%,rgba(0,0,0,.55) 100%)}
.dest .t{position:absolute;left:14px;bottom:32px;font-size:16px;font-weight:600;color:var(--white)}
.dest .s{position:absolute;left:14px;bottom:13px;font-size:13px;color:rgba(255,255,255,.9)}

/* Value band */
.band{position:absolute;left:0;top:1463px;width:1200px;height:372px;background:var(--band)}
.band h2{position:absolute;left:70px;top:71px;font-size:29px;line-height:37px;font-weight:700;color:var(--ink);letter-spacing:-.3px}
.band .lead{position:absolute;left:70px;top:168px;width:310px;font-size:14.5px;line-height:25px;color:#3b4556}
.feature{position:absolute;top:68px;width:200px;text-align:center}
.feature .icon{width:68px;height:68px;border-radius:50%;border:2.5px solid var(--green);margin:0 auto;display:flex;align-items:center;justify-content:center}
.feature h3{margin-top:21px;font-size:18px;line-height:26px;font-weight:700;color:var(--ink)}
.feature p{margin-top:14px;font-size:14.5px;line-height:25px;color:#3b4556}

/* Popular RVs */
.view-all{position:absolute;left:1060px;top:1893px;width:66px;text-align:right;font-size:14px;font-weight:600;color:var(--ink)}
.rv{position:absolute;top:1950px;width:245px;height:320px;background:var(--white);border-radius:6px;box-shadow:0 2px 10px rgba(15,30,56,.07);overflow:hidden}
.rv .pic{height:164px;position:relative}
.rv .heart{position:absolute;right:8px;top:8px}
.rv .body{padding:14px 13px 0}
.rv .title{font-size:14px;line-height:20px;font-weight:600;color:var(--ink);height:40px}
.rv .meta{margin-top:6px;font-size:12px;color:#8a8f98}
.rv .loc{margin-top:14px;font-size:12.5px;color:#3b4556}
.rv .row{margin-top:14px;display:flex;justify-content:space-between;align-items:baseline}
.rv .price{font-size:19px;font-weight:700;color:var(--ink)}
.rv .price small{font-size:12px;font-weight:400;color:#8a8f98}
.rv .rate{font-size:12.5px;color:#3b4556;display:flex;align-items:center;gap:4px}

/* CTA */
.cta{position:absolute;left:0;top:2323px;width:1200px;height:237px;background:linear-gradient(90deg,#231c18 0%,#3a2b20 35%,#2d2621 65%,#1f2228 100%)}
.cta-shade{position:absolute;inset:0;background:rgba(10,14,22,.45)}
.cta h2{position:absolute;left:0;width:1200px;top:40px;text-align:center;font-size:34px;font-weight:700;color:var(--white)}
.cta p{position:absolute;left:0;width:1200px;top:97px;text-align:center;font-size:17px;color:var(--white)}
.cta .b1{position:absolute;left:449px;top:144px;width:134px;height:43px;font-size:14px}
.cta .b2{position:absolute;left:599px;top:144px;width:143px;height:43px;font-size:14px}

/* Footer */
.footer{position:absolute;left:0;top:2560px;width:1200px;height:311px;background:var(--navy)}
.footer .brand{left:65px;top:30px;font-size:29px}
.footer .about{position:absolute;left:65px;top:90px;width:220px;font-size:12px;line-height:21px;color:#c9cfdb}
.social{position:absolute;top:186px;display:flex;gap:13px;left:67px}
.social span{width:26px;height:26px;border-radius:50%;background:var(--white)}
.col{position:absolute;top:41px}
.col h4{font-size:13.5px;font-weight:600;color:var(--white)}
.col ul{list-style:none;margin-top:16px}
.col li{font-size:12px;color:#c9cfdb;height:29px}
.col .note{margin-top:16px;font-size:12px;line-height:21px;color:#c9cfdb;width:220px}
.email{position:absolute;left:874px;top:135px;width:251px;height:42px;border-radius:6px;background:#eeeeee;font-size:12px;color:#7b808a;padding:14px}
.subscribe{position:absolute;left:874px;top:187px;width:115px;height:40px;font-size:13px}
.foot-rule{position:absolute;left:57px;top:250px;width:1086px;height:1px;background:rgba(255,255,255,.15)}
.copy{position:absolute;left:0;width:1200px;top:271px;text-align:center;font-size:13px;color:#c9cfdb}
</style>
</head>
<body>

<header class="site-nav">
  <div class="brand">Kelbrava.com <span class="brand-dot"></span></div>
  <nav class="nav-links">
    <span>How It Works</span>
    <span>List Your RV</span>
    <span>Find an RV</span>
    <span>Resources <svg width="10" height="6" viewBox="0 0 10 6"><path d="M1 1l4 4 4-4" stroke="#fff" stroke-width="1.6" fill="none"/></svg></span>
    <span>Help <svg width="10" height="6" viewBox="0 0 10 6"><path d="M1 1l4 4 4-4" stroke="#fff" stroke-width="1.6" fill="none"/></svg></span>
  </nav>
  <div class="login">Log In</div>
  <div class="btn btn-green signup">Sign Up</div>
</header>

<section class="hero" role="img" aria-label="Photo of a motorhome driving a winding mountain road beside a lake and pine forest">
  <div class="hero-shade"></div>
  <h1>The Road is<br>Yours to Share.</h1>
  <p>Rent out your RV or find the perfect one for your next adventure.</p>
  <div class="btn btn-green b1">Find an RV</div>
  <div class="btn btn-outline b2">List Your RV</div>
</section>

<form class="search">
  <div class="field" style="left:28px;width:230px"><div class="label">Location</div><div class="value">Where are you going?</div></div>
  <div class="divider" style="left:277px"></div>
  <div class="field" style="left:300px;width:197px"><div class="label">Dates</div><div class="value">Pick up – Drop off
    <svg width="17" height="17" viewBox="0 0 17 17"><rect x="1.5" y="3" width="14" height="12.5" rx="2" stroke="#6b7280" stroke-width="1.4" fill="none"/><path d="M1.5 7h14M5 1v4M12 1v4" stroke="#6b7280" stroke-width="1.4"/></svg></div></div>
  <div class="divider" style="left:525px"></div>
  <div class="field" style="left:548px;width:143px"><div class="label">Guests</div><div class="value">Add guests
    <svg width="19" height="16" viewBox="0 0 19 16"><circle cx="7" cy="5" r="3.3" stroke="#6b7280" stroke-width="1.4" fill="none"/><path d="M1 15c0-3.5 2.7-5.5 6-5.5s6 2 6 5.5M12.5 2a3.2 3.2 0 010 6.2M15 9.8c2 .7 3 2.5 3 5.2" stroke="#6b7280" stroke-width="1.4" fill="none"/></svg></div></div>
  <div class="divider" style="left:718px"></div>
  <div class="field" style="left:741px;width:134px"><div class="label">RV Type</div><div class="value" style="color:#3b4556">All RVs
    <svg width="12" height="7" viewBox="0 0 12 7"><path d="M1 1l5 5 5-5" stroke="#16233d" stroke-width="1.6" fill="none"/></svg></div></div>
  <div class="divider" style="left:902px"></div>
  <div class="btn btn-green search-btn">Search</div>
</form>

<h2 class="h2" style="top:791px">Explore by RV Type</h2>
<div class="type" style="left:68px"><div class="pic" role="img" aria-label="Illustration of a drivable camper van"></div><div class="name">Drivable<br>RVs</div></div>
<div class="type" style="left:285px"><div class="pic" role="img" aria-label="Illustration of a towable travel trailer"></div><div class="name">Towable<br>RVs</div></div>
<div class="type" style="left:504px"><div class="pic" role="img" aria-label="Illustration of a luxury motorhome"></div><div class="name">Luxury<br>RVs</div></div>
<div class="type" style="left:727px"><div class="pic" role="img" aria-label="Illustration of a pop-up camper"></div><div class="name">Pop-up<br>Campers</div></div>
<div class="type" style="left:947px"><div class="pic" role="img" aria-label="Illustration of a toy hauler trailer"></div><div class="name">Toy Haulers</div></div>
<div class="next" style="left:1127px;top:876px"><svg width="9" height="14" viewBox="0 0 9 14"><path d="M2 1l6 6-6 6" stroke="#16233d" stroke-width="2" fill="none"/></svg></div>

<h2 class="h2" style="top:1110px">Popular Destinations</h2>
<div class="dest" style="left:67px;background:linear-gradient(180deg,#8aa5c8 0%,#d9a26c 45%,#b4633a 70%,#5f6b3a 100%)" role="img" aria-label="Photo of the Grand Canyon at sunset"><div class="shade"></div><div class="t">Grand Canyon</div><div class="s">Arizona</div></div>
<div class="dest" style="left:282px;background:linear-gradient(180deg,#3e63a0 0%,#b8c6d8 40%,#dfe5ee 65%,#8d98a5 100%)" role="img" aria-label="Photo of snowy peaks in Yellowstone"><div class="shade"></div><div class="t">Yellowstone</div><div class="s">Wyoming</div></div>
<div class="dest" style="left:498px;background:linear-gradient(180deg,#7ea0c9 0%,#a5adb4 40%,#4f6b45 70%,#3c5532 100%)" role="img" aria-label="Photo of Rocky Mountain peaks above a meadow"><div class="shade"></div><div class="t">Rocky Mountain</div><div class="s">Colorado</div></div>
<div class="dest" style="left:714px;background:linear-gradient(180deg,#6f93bf 0%,#2f6c8e 40%,#1d4e6c 70%,#23384a 100%)" role="img" aria-label="Photo of the Lake Tahoe shoreline"><div class="shade"></div><div class="t">Lake Tahoe</div><div class="s">California</div></div>
<div class="dest" style="left:930px;background:linear-gradient(180deg,#6e90be 0%,#3b5a3a 45%,#2b3f3b 70%,#1f3443 100%)" role="img" aria-label="Photo of a rocky forested coast in Acadia"><div class="shade"></div><div class="t">Acadia National Park</div><div class="s">Maine</div></div>
<div class="next" style="left:1127px;top:1246px"><svg width="9" height="14" viewBox="0 0 9 14"><path d="M2 1l6 6-6 6" stroke="#16233d" stroke-width="2" fill="none"/></svg></div>

<section class="band">
  <h2>The Better Way to<br>Rent and Share RVs</h2>
  <p class="lead">Kelbrava.com is a peer-to-peer RV rental marketplace. Owners keep more of their earnings with our flat monthly rate and 20% commission per rental.</p>
  <div class="feature" style="left:464px">
    <div class="icon"><svg width="30" height="36" viewBox="0 0 30 36"><path d="M15 2v32M23 9c-1.5-2.5-4.5-3.5-8-3.5-4.5 0-8 2-8 5.5 0 8 16 4 16 12.5 0 3.5-3.5 5.5-8 5.5-4 0-7-1.5-8.5-4" stroke="#8aa633" stroke-width="3" fill="none" stroke-linecap="round"/></svg></div>
    <h3>Keep More of What<br>You Earn</h3>
    <p>We charge a flat monthly rate and 20% &amp; above commission per rental. You keep the rest.</p>
  </div>
  <div class="feature" style="left:698px">
    <div class="icon"><svg width="36" height="28" viewBox="0 0 36 28"><circle cx="13" cy="8" r="5" stroke="#8aa633" stroke-width="2.6" fill="none"/><circle cx="25" cy="9" r="4" stroke="#8aa633" stroke-width="2.6" fill="none"/><path d="M3 26c0-6 4.5-9 10-9s10 3 10 9zM22 17c6 0 11 2.5 11 9h-8" stroke="#8aa633" stroke-width="2.6" fill="none" stroke-linejoin="round"/></svg></div>
    <h3>Peer-to-Peer<br>Community</h3>
    <p>Connect with RV owners and renters who love adventure as much as you do.</p>
  </div>
  <div class="feature" style="left:900px">
    <div class="icon"><svg width="30" height="34" viewBox="0 0 30 34"><path d="M15 2l12 4.5v9c0 8-5.5 13.5-12 16.5C8.5 29 3 23.5 3 15.5v-9z" stroke="#8aa633" stroke-width="2.6" fill="none" stroke-linejoin="round"/><path d="M9.5 16.5l4 4 7-8" stroke="#8aa633" stroke-width="2.6" fill="none" stroke-linecap="round"/></svg></div>
    <h3>We're Here<br>to Help</h3>
    <p>24/7 support and protection for peace of mind on every journey.</p>
  </div>
</section>

<h2 class="h2" style="top:1886px">Popular RVs</h2>
<div class="view-all">View all</div>

<article class="rv" style="left:68px">
  <div class="pic" role="img" aria-label="Photo of a Class C motorhome" style="background:linear-gradient(180deg,#8fb3d9 0%,#d9d2c4 50%,#6b8a4a 100%)"><svg class="heart" width="24" height="22" viewBox="0 0 24 22"><path d="M12 20S2 14 2 7.5A5 5 0 0112 5a5 5 0 0110 2.5C22 14 12 20 12 20z" stroke="#fff" stroke-width="2" fill="none"/></svg></div>
  <div class="body"><div class="title">2021 Halvern Coach<br>Meridian 31W</div><div class="meta">Sleeps 7 &nbsp;•&nbsp; Class C</div><div class="loc">Denver, CO</div>
  <div class="row"><div class="price">$195 <small>/night</small></div><div class="rate"><svg width="12" height="12" viewBox="0 0 12 12"><path d="M6 .5l1.7 3.6 3.8.4-2.9 2.6.9 3.9L6 9 2.5 11l.9-3.9L.5 4.5l3.8-.4z" fill="#8aa633"/></svg>4.9 (36)</div></div></div>
</article>
<article class="rv" style="left:334px">
  <div class="pic" role="img" aria-label="Photo of a bunkhouse travel trailer" style="background:linear-gradient(180deg,#8eb0d3 0%,#e2e4e6 50%,#5d6b55 100%)"><svg class="heart" width="24" height="22" viewBox="0 0 24 22"><path d="M12 20S2 14 2 7.5A5 5 0 0112 5a5 5 0 0110 2.5C22 14 12 20 12 20z" stroke="#fff" stroke-width="2" fill="none"/></svg></div>
  <div class="body"><div class="title">2022 Corvale Trail Flight<br>Bunkhouse</div><div class="meta">Sleeps 8 &nbsp;•&nbsp; Travel Trailer</div><div class="loc">Boise, ID</div>
  <div class="row"><div class="price">$120 <small>/night</small></div><div class="rate"><svg width="12" height="12" viewBox="0 0 12 12"><path d="M6 .5l1.7 3.6 3.8.4-2.9 2.6.9 3.9L6 9 2.5 11l.9-3.9L.5 4.5l3.8-.4z" fill="#8aa633"/></svg>4.8 (27)</div></div></div>
</article>
<article class="rv" style="left:602px">
  <div class="pic" role="img" aria-label="Photo of a Class B camper van" style="background:linear-gradient(180deg,#b9c6cf 0%,#b7b3ab 50%,#5c6a4c 100%)"><svg class="heart" width="24" height="22" viewBox="0 0 24 22"><path d="M12 20S2 14 2 7.5A5 5 0 0112 5a5 5 0 0110 2.5C22 14 12 20 12 20z" stroke="#fff" stroke-width="2" fill="none"/></svg></div>
  <div class="body"><div class="title">2020 Tamsyn<br>Vista 59P</div><div class="meta">Sleeps 4 &nbsp;•&nbsp; Class B</div><div class="loc">Portland, OR</div>
  <div class="row"><div class="price">$175 <small>/night</small></div><div class="rate"><svg width="12" height="12" viewBox="0 0 12 12"><path d="M6 .5l1.7 3.6 3.8.4-2.9 2.6.9 3.9L6 9 2.5 11l.9-3.9L.5 4.5l3.8-.4z" fill="#8aa633"/></svg>4.9 (42)</div></div></div>
</article>
<article class="rv" style="left:869px">
  <div class="pic" role="img" aria-label="Photo of a toy hauler trailer" style="background:linear-gradient(180deg,#a9c1da 0%,#cfd2d6 50%,#4a4f55 100%)"><svg class="heart" width="24" height="22" viewBox="0 0 24 22"><path d="M12 20S2 14 2 7.5A5 5 0 0112 5a5 5 0 0110 2.5C22 14 12 20 12 20z" stroke="#fff" stroke-width="2" fill="none"/></svg></div>
  <div class="body"><div class="title">2021 Pinecrest<br>XTR Haul 31QB</div><div class="meta">Sleeps 6 &nbsp;•&nbsp; Toy Hauler</div><div class="loc">Las Vegas, NV</div>
  <div class="row"><div class="price">$140 <small>/night</small></div><div class="rate"><svg width="12" height="12" viewBox="0 0 12 12"><path d="M6 .5l1.7 3.6 3.8.4-2.9 2.6.9 3.9L6 9 2.5 11l.9-3.9L.5 4.5l3.8-.4z" fill="#8aa633"/></svg>4.7 (19)</div></div></div>
</article>
<div class="next" style="left:1127px;top:2052px"><svg width="9" height="14" viewBox="0 0 9 14"><path d="M2 1l6 6-6 6" stroke="#16233d" stroke-width="2" fill="none"/></svg></div>

<section class="cta" role="img" aria-label="Evening photo of campers gathered around a fire beside a travel trailer under string lights">
  <div class="cta-shade"></div>
  <h2>Ready for Your Next Adventure?</h2>
  <p>Join thousands of RV owners and adventurers on Kelbrava.com</p>
  <div class="btn btn-green b1">Find an RV</div>
  <div class="btn btn-outline b2">List Your RV</div>
</section>

<footer class="footer">
  <div class="brand">Kelbrava.com <span class="brand-dot"></span></div>
  <p class="about">Kelbrava.com is the peer-to-peer RV rental marketplace that helps owners share their RVs and adventurers find the perfect ride.</p>
  <div class="social"><span></span><span></span><span></span></div>
  <div class="col" style="left:329px"><h4>Explore</h4><ul><li>Find an RV</li><li>List Your RV</li><li>How It Works</li><li>Destinations</li><li>Gift Cards</li></ul></div>
  <div class="col" style="left:505px"><h4>Resources</h4><ul><li>Help Center</li><li>RV Travel Guide</li><li>Safety Tips</li><li>Insurance</li><li>Blog</li></ul></div>
  <div class="col" style="left:692px"><h4>Company</h4><ul><li>About Us</li><li>Careers</li><li>Press</li><li>Terms &amp; Conditions</li><li>Privacy Policy</li></ul></div>
  <div class="col" style="left:874px"><h4>Stay in the Loop</h4><p class="note">Get tips, deals, and RV inspiration straight to your inbox.</p></div>
  <div class="email">Enter your email</div>
  <div class="btn btn-green subscribe">Subscribe</div>
  <div class="foot-rule"></div>
  <div class="copy">© 2026 kelbrava.com, All rights reserved.</div>
</footer>

</body>
</html>
```